I have a logo and need to design the business card and stationery.
Updates

The uploaded logo image named as GREYMARSH CONSTRUCTION which is to be replaced to GREYMARSH CONTRACTS. Kindly add below details and submit the designs- Company name- Greymarsh Engineering Contracts LLP Name & Post- Kelvan Joshi (Designated Partner) Address- Block No.317, Wing C, Tulvo Trade Court, Manek Pural Road, Ruparel Industrial Estate, Goregaon(E), Mumbai - 400 063 Contact- +91 97415 60382 Email- kelvanjoshi@mailbrook.example Website- www.greymarshcontracts.example Contact for Letterhead- +91-22-28754193

Hi Tovin Rahul, We are liking your Design #28860835. We have suggested some changes which are mentioned in feedback. Kindly revert with it asap to finalize this design.

Colors

Designer to choose colors to be used in the design.

```html
<!DOCTYPE html>
<html lang="en">
<head>
<meta charset="utf-8">
<title>Greymarsh Contracts – Business Card</title>
<link rel="stylesheet" href="https://fonts.googleapis.com/css2?family=Montserrat:wght@400;500;600&family=Rubik:wght@700&display=swap">
<style>
  :root {
    --canvas: #d8d8d8;
    --card-white: #ffffff;
    --charcoal: #333436;
    --stripe: #5c5d60;
    --ink: #4a4a4c;
    --ink-soft: #3c3c3e;
    --band-text: #c9c9cb;
    --ghost: #5a5b5e;
  }
  * { box-sizing: border-box; margin: 0; padding: 0; }
  html, body { width: 1200px; height: 848px; overflow: hidden; }
  body {
    background: var(--canvas);
    font-family: "Montserrat", sans-serif;
    position: relative;
  }
  .card {
    position: absolute;
    top: 269px;
    width: 540px;
    height: 310px;
    overflow: hidden;
    box-shadow: 0 6px 18px rgba(0,0,0,0.12);
  }
  .card--front { left: 40px; background: var(--card-white); }
  .card--back  { left: 620px; background: var(--charcoal); }

  /* Front */
  .brand {
    position: absolute;
    display: flex;
    align-items: center;
    gap: 8px;
    color: var(--ink);
    font-weight: 600;
    letter-spacing: 0.06em;
  }
  .brand__mark { background: currentColor; flex: none; }
  .card--front .brand { left: 150px; top: 58px; font-size: 20px; }
  .card--front .brand__mark { width: 18px; height: 18px; }

  .person { position: absolute; left: 34px; top: 128px; }
  .person__name {
    font-family: "Rubik", sans-serif;
    font-weight: 700;
    font-size: 22px;
    color: var(--ink);
  }
  .person__role {
    font-size: 10px;
    letter-spacing: 0.02em;
    color: var(--ink-soft);
    margin-top: 3px;
  }

  .contacts {
    position: absolute;
    left: 270px;
    top: 116px;
    list-style: none;
    font-size: 11px;
    color: var(--ink-soft);
  }
  .contacts li { display: flex; align-items: center; gap: 7px; height: 20px; }
  .contacts svg { width: 13px; height: 13px; flex: none; }

  .band {
    position: absolute;
    left: 0; right: 0; bottom: 0;
    height: 100px;
    background: var(--charcoal);
    border-top: 6px solid var(--stripe);
    padding: 28px 34px 0 60px;
    color: var(--band-text);
    font-size: 11.5px;
    line-height: 1.55;
  }

  /* Back */
  .card--back .brand {
    left: 0; right: 0; top: 0; bottom: 0;
    justify-content: center;
    color: var(--ghost);
    font-size: 30px;
    gap: 12px;
  }
  .card--back .brand__mark { width: 26px; height: 26px; }
</style>
</head>
<body>

  <section class="card card--front" aria-label="Business card front">
    <div class="brand">
      <span class="brand__mark"></span>
      <span class="brand__name">GREYMARSH CONTRACTS</span>
    </div>

    <div class="person">
      <p class="person__name">Kelvan Joshi</p>
      <p class="person__role">DESIGNATED PARTNER</p>
    </div>

    <ul class="contacts">
      <li>
        <svg viewBox="0 0 24 24" fill="none" stroke="currentColor" stroke-width="1.6"><path d="M5 3h4l2 5-2.5 1.5a11 11 0 0 0 6 6L16 13l5 2v4a2 2 0 0 1-2 2A17 17 0 0 1 3 5a2 2 0 0 1 2-2z"/></svg>
        <span>+91 97415 60382</span>
      </li>
      <li>
        <svg viewBox="0 0 24 24" fill="none" stroke="currentColor" stroke-width="1.6"><rect x="3" y="5" width="18" height="14"/><path d="M3 5l9 8 9-8"/></svg>
        <span>kelvanjoshi@mailbrook.example</span>
      </li>
      <li>
        <svg viewBox="0 0 24 24" fill="none" stroke="currentColor" stroke-width="1.6"><circle cx="12" cy="12" r="9"/><path d="M3 12h18M12 3c3 3 3 15 0 18M12 3c-3 3-3 15 0 18"/></svg>
        <span>www.greymarshcontracts.example</span>
      </li>
    </ul>

    <div class="band">
      <p>Block No. 317, Wing C, Tulvo Trade Court, Manek Pural Road,</p>
      <p>Ruparel Industrial Estate, Goregaon(E), Mumbai - 400 063</p>
    </div>
  </section>

  <section class="card card--back" aria-label="Business card back">
    <div class="brand">
      <span class="brand__mark"></span>
      <span class="brand__name">GREYMARSH CONTRACTS</span>
    </div>
  </section>

</body>
</html>
```